Basic business card

use my newly created logo - and the phrases (Lower Cost of Test & Accelarated New Product Introduction) - and my new email domain / ID - use at conferences / tradeshows

Industry/Entity Type

semiconductor

Contact Information for Business Card

Daniel K Forde, Owner, communicate via Logo - Lower COT - Cost of Test, Accelerated NPI - New Product Introduction, phone +1 555 613 0946, Chandler, Arizona, USA, daniel.forde@qal-vub.com

Font styles to use
Sans Serif

Requirements
Nice to have
• re-use my logo created via Pixel Harbor last August (#7315926)

```html
<!DOCTYPE html>
<html lang="en">
<head>
<meta charset="utf-8">
<title>QAL-VUB Business Card</title>
<link href="https://fonts.googleapis.com/css2?family=Open+Sans:wght@400;600;700&display=swap" rel="stylesheet">
<style>
  :root {
    --backdrop: #303030;
    --card: #1f2023;
    --logo-slate: #56657f;
    --logo-silver: #8a96a8;
    --orange: #f7941d;
    --blue: #1476c6;
    --white: #f2f2f2;
    --deco: #2a2d33;
  }
  * { margin: 0; padding: 0; box-sizing: border-box; }
  html, body { width: 1200px; height: 779px; overflow: hidden; }
  body {
    background: var(--backdrop);
    font-family: "Open Sans", sans-serif;
    display: flex; align-items: center; justify-content: center; gap: 30px;
  }
  .card {
    position: relative; width: 560px; height: 320px;
    background: var(--card); overflow: hidden;
    box-shadow: 0 10px 30px rgba(0,0,0,.45);
  }
  .brand {
    display: flex; align-items: center; gap: 10px;
    font-weight: 600; letter-spacing: 2px; color: var(--logo-slate);
  }
  .brand-mark { background: var(--blue); }
  .card-back .brand {
    position: absolute; inset: 0; justify-content: center;
    font-size: 52px; color: var(--logo-silver);
  }
  .card-back .brand-mark { width: 26px; height: 26px; }
  .card-front .brand {
    position: absolute; left: 26px; top: 30px; font-size: 30px;
  }
  .card-front .brand-mark { width: 16px; height: 16px; }
  .logo-watermark {
    position: absolute; left: 330px; top: 62px; width: 200px; height: 170px;
    background: linear-gradient(135deg, #3a3328 0%, #2b3a36 45%, #29323f 100%);
    opacity: .55;
  }
  .identity {
    position: absolute; right: 34px; top: 70px; text-align: right;
  }
  .person-name { font-size: 26px; font-weight: 700; line-height: 1.1; }
  .person-name .first { color: var(--orange); }
  .person-name .last { color: var(--blue); }
  .person-title { color: var(--white); font-size: 15px; font-weight: 600; margin-top: 2px; }
  .accent-bar {
    position: absolute; right: 10px; top: 66px; width: 16px; height: 52px;
    background: var(--orange);
  }
  .divider {
    position: absolute; left: 60px; right: 20px; top: 130px; height: 1.5px;
    background: var(--blue);
  }
  .contacts {
    position: absolute; left: 28px; top: 176px; list-style: none;
    color: var(--white); font-size: 15px; line-height: 24px;
  }
  .contacts li { display: flex; align-items: center; gap: 10px; }
  .contacts svg { width: 14px; height: 14px; fill: var(--orange); }
  .address {
    position: absolute; right: 30px; top: 196px; text-align: right;
    color: var(--white); font-size: 14px; line-height: 19px;
  }
  .bands { position: absolute; left: 0; bottom: 0; width: 560px; height: 70px; }
</style>
</head>
<body>
  <section class="card card-back">
    <div class="brand"><span class="brand-mark"></span>QAL-VUB</div>
  </section>

  <section class="card card-front">
    <div class="brand"><span class="brand-mark"></span>QAL-VUB</div>
    <div class="logo-watermark" role="img" aria-label="Faint enlarged company emblem in the background"></div>

    <div class="accent-bar"></div>
    <div class="identity">
      <p class="person-name"><span class="first">Lena</span> <span class="last">Marvik</span></p>
      <p class="person-title">Managing Director</p>
    </div>
    <div class="divider"></div>

    <ul class="contacts">
      <li><svg viewBox="0 0 24 24"><path d="M6.6 10.8a15 15 0 0 0 6.6 6.6l2.2-2.2c.3-.3.7-.4 1-.2 1.1.4 2.3.6 3.6.6.6 0 1 .4 1 1V20c0 .6-.4 1-1 1A17 17 0 0 1 3 4c0-.6.4-1 1-1h3.5c.6 0 1 .4 1 1 0 1.3.2 2.5.6 3.6.1.3 0 .7-.2 1z"/></svg>(555) 201-4837</li>
      <li><svg viewBox="0 0 24 24"><path d="M2 6h20v12H2z M2 6l10 7 10-7" fill="none" stroke="#f7941d" stroke-width="2"/></svg>info@qal-vub.com</li>
      <li><svg viewBox="0 0 24 24"><circle cx="12" cy="12" r="9" fill="none" stroke="#f7941d" stroke-width="2"/><path d="M3 12h18M12 3c3 3 3 15 0 18M12 3c-3 3-3 15 0 18" fill="none" stroke="#f7941d" stroke-width="1.6"/></svg>www.qal-vub.com</li>
    </ul>

    <p class="address">418 Harlow Ave. Suite 310<br>Mesa Grove, TX 75990</p>

    <svg class="bands" viewBox="0 0 560 70" aria-hidden="true">
      <polygon points="0,50 420,50 432,42 560,8 560,70 0,70" fill="#1476c6"/>
      <polygon points="0,40 410,40 416,36 0,36" fill="#f7941d"/>
      <rect x="0" y="38" width="412" height="7" fill="#f7941d"/>
    </svg>
  </section>
</body>
</html>
```